BOLD & MINIMALIST DESIGN NEEDED

We want a very bold but minimalistic business card design that is impactful and utilizes both sides of the business card. Our current logo is included for your use.

We want bold fonts and good use of negative space. We don't want the logo to overpower the design.

Target Market(s)

Professionals who are building new commercial buildings.

Industry/Entity Type

Construction

Contact Information for Business Card

Name, Title, email, office phone, cell phone, website

Font styles to use
Serif
Sans Serif

Requirements
Must have
• Bold design!

```html
<!DOCTYPE html>
<html lang="en">
<head>
<meta charset="utf-8">
<title>Ridgeline – Business Card</title>
<link href="https://fonts.googleapis.com/css2?family=Oswald:wght@600&family=Montserrat:wght@400&display=swap" rel="stylesheet">
<style>
  :root {
    --backdrop: #161616;
    --card-white: #ffffff;
    --band-dark: #2a2a2a;
    --accent-green: #7dc42a;
    --ink-black: #151515;
    --text-light: #f2f2f2;
    --back-top: #2c2c2c;
    --back-bottom: #1f1f1f;
    --back-brand: #3b3b3b;
  }
  * { margin: 0; padding: 0; box-sizing: border-box; }
  html, body {
    width: 1200px; height: 897px; overflow: hidden;
    background: var(--backdrop);
  }
  .canvas { position: relative; width: 1200px; height: 897px; }

  .card {
    position: absolute; left: 304px; width: 594px; height: 338px;
    border-radius: 18px; overflow: hidden;
  }
  .card-front { top: 92px; background: var(--card-white); }
  .card-back {
    top: 470px;
    background: linear-gradient(160deg, var(--back-top), var(--back-bottom));
  }

  .brand-front {
    position: absolute; top: 36px; right: 34px;
    display: flex; align-items: center; gap: 12px;
  }
  .brand-square { width: 22px; height: 22px; background: var(--accent-green); }
  .brand-name {
    font-family: "Oswald", sans-serif; font-weight: 600;
    font-size: 42px; letter-spacing: 1px; line-height: 1;
    color: var(--ink-black);
  }

  .contact-band {
    position: absolute; left: 0; top: 157px; width: 374px; height: 165px;
    background: var(--band-dark);
    padding: 12px 0 0 30px;
  }
  .person-name {
    font-family: "Oswald", sans-serif; font-weight: 600;
    font-size: 33px; line-height: 1; letter-spacing: 0.3px;
    color: var(--accent-green); text-transform: uppercase;
  }
  .person-title {
    font-family: "Montserrat", sans-serif; font-size: 14px;
    color: var(--text-light); margin-top: 4px; letter-spacing: 0.5px;
  }
  .contact-list { list-style: none; margin-top: 16px; }
  .contact-list li {
    display: flex; align-items: center; gap: 5px;
    font-family: "Montserrat", sans-serif; font-size: 14px;
    line-height: 18px; color: var(--text-light);
  }
  .contact-list svg { width: 13px; height: 13px; flex: none; }
  .highlight { color: var(--accent-green); }

  .brand-back {
    position: absolute; inset: 0;
    display: flex; align-items: center; justify-content: center;
    font-family: "Oswald", sans-serif; font-weight: 600;
    font-size: 56px; letter-spacing: 3px; color: var(--back-brand);
  }
</style>
</head>
<body>
<div class="canvas">
  <section class="card card-front">
    <div class="brand-front">
      <span class="brand-square"></span>
      <span class="brand-name">RIDGELINE</span>
    </div>
    <div class="contact-band">
      <h1 class="person-name">Marcus Bell</h1>
      <p class="person-title">OWNER</p>
      <ul class="contact-list">
        <li>
          <svg viewBox="0 0 16 16" aria-hidden="true"><path fill="#7dc42a" d="M3.5 1l3 3-1.6 1.8c.8 1.9 2.4 3.5 4.3 4.3L11 8.5l3 3-2 2.5C6.5 13.5 2.5 9.5 1 4z"/></svg>
          (555) 014-2276
        </li>
        <li>
          <svg viewBox="0 0 16 16" aria-hidden="true"><path fill="#7dc42a" d="M1 6c1-3 13-3 14 0l-1 2-3-1V5.5c-2-.6-4-.6-6 0V7L2 8zM4 8h8l2 6H2zm4 1.5a2 2 0 100 4 2 2 0 000-4z"/></svg>
          (555) 014-2277
        </li>
        <li>
          <svg viewBox="0 0 16 16" aria-hidden="true"><rect x="1.5" y="3.5" width="13" height="9" fill="none" stroke="#7dc42a" stroke-width="1.4"/><path d="M1.5 3.5L8 9l6.5-5.5" fill="none" stroke="#7dc42a" stroke-width="1.4"/></svg>
          ridgelinebuild@mail.com
        </li>
        <li>
          <svg viewBox="0 0 16 16" aria-hidden="true"><g fill="none" stroke="#7dc42a" stroke-width="1.2"><circle cx="8" cy="8" r="6.5"/><ellipse cx="8" cy="8" rx="3" ry="6.5"/><path d="M1.5 8h13M2.5 4.8h11M2.5 11.2h11"/></g></svg>
          www.<span class="highlight">ridgelinebuild</span>.com
        </li>
      </ul>
    </div>
  </section>

  <section class="card card-back">
    <div class="brand-back">RIDGELINE</div>
  </section>
</div>
</body>
</html>
```